Can You Break Boring? - Design a Dazzling Conference Program!

The 35th Annual BRQL Summit and Expo Fair is the Top-Notch event for Veterinary Technicians in Canada. With a reputation like that, the program has to knock the delegates socks off!
Are you up to the challenge?
The BRQL will provide you with the following:
-venue information (hours, floorplan etc.)
-conference logo and theme
-speaker bios and lecture abstracts (58 speakers, over 108 sessions)
-4 day agenda
-images that have been used in marketing to date
-color schemes that are preferred
We are looking for someone to take the material and create a program that is colorful, engaging and unique.
A copy of the registration brochure is attached. The winning submission will strongly resemble this document.
Updates

Project Deadline Extended
Reason: The submissions are getting closer to what we are looking for so we wish to extend the deadline to provide designers more time to submit more ideas.

Project Deadline Extended
Reason: I am looking for more concepts on the interior layout now. Please submit your ideas for: - exhibitor info pages - speaker info/lecture info pages - venue info - floorplan and agenda pages.

Target Market(s)

approx. 1200 Veterinary Technician delegates attending the conference

Industry/Entity Type

Marketing

Requirements
Must have
• - conference logo and theme (provided)
- BRQL logo (provided)
- venue floor plans
- conference schedule
- speaker bios and session abstracts
STRONG relation to the registration brochure.

```html
<!DOCTYPE html>
<html lang="en">
<head>
<meta charset="utf-8">
<title>35th Annual BRQL Summit &amp; Expo Fair</title>
<link rel="stylesheet" href="https://fonts.googleapis.com/css2?family=Cormorant+Garamond:wght@700&family=Marcellus&family=EB+Garamond:wght@400;600&display=swap">
<style>
  :root {
    --magenta: #a2317f;
    --violet: #6b2c8c;
    --indigo: #2f3f94;
    --blue: #1f62a7;
    --cyan: #2bb0d2;
    --leaf: #3aa866;
    --forest: #0b7a3d;
    --title: #5a2d8e;
    --ink: #111111;
  }
  html, body {
    margin: 0;
    padding: 0;
    width: 927px;
    height: 1200px;
    overflow: hidden;
  }
  .cover {
    position: relative;
    width: 927px;
    height: 1200px;
    overflow: hidden;
  }
  .backdrop {
    position: absolute;
    inset: 0;
    background: linear-gradient(90deg,
      var(--magenta) 0%,
      var(--violet) 20%,
      var(--indigo) 38%,
      var(--blue) 52%,
      var(--cyan) 64%,
      var(--leaf) 74%,
      var(--forest) 100%);
  }
  .lens {
    position: absolute;
    inset: 0;
    width: 927px;
    height: 1200px;
  }
  .cover-text {
    position: absolute;
    inset: 0;
    text-align: center;
    color: var(--ink);
  }
  .edition {
    position: absolute;
    top: 100px;
    width: 100%;
    margin: 0;
    font-family: "EB Garamond", serif;
    font-weight: 400;
    font-size: 62px;
    line-height: 1;
  }
  .edition strong { font-weight: 600; }
  .edition sup { font-size: 28px; vertical-align: 26px; }
  .acronym {
    position: absolute;
    top: 184px;
    width: 100%;
    margin: 0;
    font-family: "Cormorant Garamond", serif;
    font-weight: 700;
    font-size: 330px;
    line-height: 1;
    letter-spacing: -4px;
    color: var(--title);
  }
  .event-name {
    position: absolute;
    top: 538px;
    width: 100%;
    margin: 0;
    font-family: "Marcellus", serif;
    font-weight: 400;
    font-size: 66px;
    line-height: 1;
  }
  .venue {
    position: absolute;
    top: 632px;
    width: 100%;
    margin: 0;
    font-family: "Marcellus", serif;
    font-weight: 400;
    font-size: 33px;
    line-height: 1;
  }
  .dates {
    position: absolute;
    top: 722px;
    width: 100%;
    margin: 0;
    font-family: "EB Garamond", serif;
    font-size: 28px;
    line-height: 1;
  }
</style>
</head>
<body>
<main class="cover">
  <div class="backdrop" role="img" aria-label="Vertical streaked spectrum background from magenta through blue to green"></div>

  <svg class="lens" viewBox="0 0 927 1200" aria-hidden="true">
    <defs>
      <linearGradient id="lens-fill" x1="0" y1="0" x2="0" y2="1">
        <stop offset="0" stop-color="#dcdcdc"/>
        <stop offset="0.45" stop-color="#ffffff"/>
        <stop offset="0.62" stop-color="#f2f2f2"/>
        <stop offset="1" stop-color="#cfcfcf"/>
      </linearGradient>
      <filter id="lens-shadow" x="-10%" y="-10%" width="120%" height="130%">
        <feDropShadow dx="0" dy="8" stdDeviation="8" flood-color="#000" flood-opacity="0.45"/>
      </filter>
    </defs>
    <path d="M0 100 Q463 -40 927 100 L927 712 Q463 870 0 712 Z" fill="url(#lens-fill)" filter="url(#lens-shadow)"/>
  </svg>

  <header class="cover-text">
    <p class="edition"><strong>35<sup>th</sup></strong> Annual</p>
    <h1 class="acronym">BRQL</h1>
    <h2 class="event-name">Summit &amp; Expo Fair</h2>
    <p class="venue">Riverside Convention Centre &amp; Harbourview Hotel</p>
    <p class="dates">February 21-23, 2013</p>
  </header>
</main>
</body>
</html>
```